Business Card Design

New business card design

Target Market(s)

Residential & Commercial Property Managers

Industry/Entity Type

Plumbing Services

Contact Information for Business Card

Name - Rowan Keddle, title - Director, Phone Number - 0431 286 517, email - rowan@tbk-plumbing.com.au, Company ABN - 73 215 904 386,

Font styles to use
Sans Serif

Colors
0054AA
0677BA
7BADD7
CADEEF
E8F1F8

```html
<!DOCTYPE html>
<html lang="en">
<head>
<meta charset="utf-8">
<title>TBK Plumbing Services – Business Card</title>
<link rel="stylesheet" href="https://fonts.googleapis.com/css2?family=Montserrat:wght@400;500;600&display=swap">
<style>
  :root {
    --page-bg: #1c1d1f;
    --card-light: #f3f3f3;
    --card-dark: #1d232a;
    --ink: #1f2a33;
    --accent: #2a9fd8;
    --white: #ffffff;
  }
  * { margin: 0; padding: 0; box-sizing: border-box; }
  html, body {
    width: 1200px;
    height: 1059px;
    overflow: hidden;
    background: var(--page-bg);
    font-family: "Montserrat", sans-serif;
  }
  .canvas { position: relative; width: 1200px; height: 1059px; }

  .card {
    position: absolute;
    border-radius: 24px;
    overflow: hidden;
  }
  .card-front {
    left: 256px; top: 89px;
    width: 688px; height: 390px;
    background: var(--card-light);
    color: var(--ink);
  }
  .card-back {
    left: 254px; top: 547px;
    width: 693px; height: 393px;
    background: var(--card-dark);
    color: var(--white);
  }

  .brand {
    position: absolute;
    display: flex;
    align-items: center;
    gap: 10px;
    font-weight: 500;
    white-space: nowrap;
  }
  .brand-dot {
    border-radius: 50%;
    background: var(--accent);
    flex: none;
  }
  .card-front .brand {
    left: 60px; width: 254px; top: 172px;
    justify-content: center;
    font-size: 20px;
    color: var(--ink);
  }
  .card-front .brand-dot { width: 14px; height: 14px; }
  .card-back .brand {
    left: 0; right: 0; top: 172px;
    justify-content: center;
    font-size: 36px;
    color: var(--white);
    gap: 16px;
  }
  .card-back .brand-dot { width: 24px; height: 24px; }

  .divider {
    position: absolute;
    left: 344px; top: 121px;
    width: 1px; height: 150px;
    background: var(--accent);
  }

  .contact {
    position: absolute;
    left: 373px; top: 114px;
  }
  .contact-name {
    font-size: 27px;
    font-weight: 600;
    color: var(--accent);
    line-height: 1.1;
  }
  .contact-title {
    font-size: 17px;
    font-weight: 400;
    line-height: 1.2;
  }
  .contact-abn {
    margin-top: 20px;
    font-size: 18px;
    letter-spacing: 0.3px;
  }
  .contact-abn .label { color: var(--accent); }
  .contact-lines { margin-top: 21px; list-style: none; }
  .contact-lines li {
    display: flex;
    align-items: center;
    gap: 8px;
    font-size: 18px;
    line-height: 26px;
  }
  .contact-lines svg { width: 12px; height: 12px; flex: none; }
</style>
</head>
<body>
<main class="canvas">

  <section class="card card-front" aria-label="Business card front">
    <div class="brand"><span class="brand-dot"></span>TBK Plumbing Services</div>
    <div class="divider"></div>
    <div class="contact">
      <p class="contact-name">Rowan Keddle</p>
      <p class="contact-title">Director</p>
      <p class="contact-abn"><span class="label">ABN</span> - 73 215 904 386</p>
      <ul class="contact-lines">
        <li>
          <svg viewBox="0 0 24 24" aria-hidden="true"><path fill="#2a9fd8" d="M6.6 10.8a15.1 15.1 0 0 0 6.6 6.6l2.2-2.2a1 1 0 0 1 1-.25 11.4 11.4 0 0 0 3.6.57 1 1 0 0 1 1 1V20a1 1 0 0 1-1 1A17 17 0 0 1 3 4a1 1 0 0 1 1-1h3.5a1 1 0 0 1 1 1c0 1.25.2 2.45.57 3.57a1 1 0 0 1-.25 1z"/></svg>
          0431 286 517
        </li>
        <li>
          <svg viewBox="0 0 24 24" aria-hidden="true"><rect x="1" y="4" width="22" height="16" fill="#2a9fd8"/><path d="M1 4l11 9 11-9M1 20l8-8M23 20l-8-8" stroke="#f3f3f3" stroke-width="2" fill="none"/></svg>
          rowan@tbk-plumbing.com.au
        </li>
      </ul>
    </div>
  </section>

  <section class="card card-back" aria-label="Business card back">
    <div class="brand"><span class="brand-dot"></span>TBK Plumbing Services</div>
  </section>

</main>
</body>
</html>
```